Dovin Sound 862 the new wave for sound to enlighten open ears

This is a music recording studio, we need pictures of a booth, random pictures of anything that will draw interest to a recording studio, we just need the website to reflect a music studio recording website. Apply generic information on the site that correlates with most music studio websites up to date. We want the modern style look that will entice eyes across the nation. Information should be easily accessible on the website. Dovin Sound 862 is owned by Marcellus Okafor located 5176 Bellweather Ln, Larkfield, Fl, 34719. Email: Mokaforsound@trellomail.net and best contact number to date is 417-293-7041. The sound coming out of this location will be radio ready at all times, artist come in one way and come out with more wisdom than before. Its the new way to make music the appropriate way and bring the best out of those willing to reach their peak.

Target Market(s)

Recording Artist

Industry/Entity Type

Recording Studio

Coding

Coded - Design and coding required

Number of Pages Required

1 page

Font styles to use
Sans Serif

Requirements
Must have
• Anything that gives the site a music feel
Nice to have
• microphones, booths, studio mixing desk

```html
<!DOCTYPE html>
<html lang="en">
<head>
<meta charset="utf-8">
<title>Dovin Sound 862 — Music Recording Studio</title>
<link href="https://fonts.googleapis.com/css2?family=Open+Sans:wght@400;600;700&family=Roboto:wght@300;400;700&display=swap" rel="stylesheet">
<style>
:root{
  --orange:#f7860f;
  --blue:#2ec7f0;
  --dark:#454545;
  --ink:#333;
  --muted:#8a8a8a;
  --line:#e6e6e6;
  --soft:#f4f4f4;
  --white:#fff;
}
*{box-sizing:border-box;margin:0;padding:0}
html,body{width:1200px;height:3147px;overflow:hidden}
body{position:relative;background:var(--white);font-family:"Open Sans",Arial,sans-serif;color:var(--ink)}
.abs{position:absolute}

/* header */
.topline{left:0;top:0;width:1200px;height:4px;background:linear-gradient(90deg,var(--orange),var(--blue) 40%,var(--blue) 60%,var(--orange))}
.site-header{left:0;top:4px;width:1200px;height:126px}
.brand{left:130px;top:30px;display:flex;align-items:center;gap:14px}
.brand-dot{width:62px;height:62px;border-radius:50%;background:var(--blue);border:5px solid #bfeefb}
.brand-name{font-family:"Roboto",Arial,sans-serif;font-size:30px;font-weight:400;color:#3a3a3a}
.nav{right:130px;top:52px;display:flex;gap:44px;font-size:14px;color:#333}
.nav .active{color:var(--blue)}
.search{right:130px;top:54px}

/* hero */
.hero{left:0;top:130px;width:1200px;height:600px;background:radial-gradient(ellipse at 50% 45%,#8a5a32 0%,#4b2e1a 45%,#1e140d 100%)}
.hero-title{left:0;top:160px;width:1200px;text-align:center;color:var(--white);font-family:"Roboto",Arial,sans-serif;text-shadow:0 2px 8px rgba(0,0,0,.4)}
.hero-title .l1{display:block;font-size:72px;font-weight:300;line-height:80px}
.hero-title .l2{display:block;font-size:72px;font-weight:700;line-height:84px}
.btn{display:inline-block;border-radius:22px;color:var(--white);font-size:13px;text-align:center}
.hero-btn{left:512px;top:352px;width:176px;height:42px;line-height:42px;background:var(--orange)}
.hero-arrow{top:242px;width:52px;height:52px;border-radius:50%;background:rgba(0,0,0,.45)}
.hero-arrow.prev{left:80px}.hero-arrow.next{right:80px}
.hero-curve{left:0;top:460px}

/* section heads */
.sec-title{left:0;width:1200px;text-align:center;font-family:"Roboto",Arial,sans-serif;font-weight:300;font-size:36px;color:#3d3d3d}
.sec-sub{left:290px;width:620px;text-align:center;font-size:11px;line-height:23px;color:var(--muted)}

/* services */
.service{top:912px;width:290px;text-align:center}
.service-icon{width:136px;height:136px;margin:0 auto;border-radius:50%;border:2px solid var(--blue);display:flex;align-items:center;justify-content:center}
.service h3{margin-top:26px;font-size:13px;font-weight:600;color:#333}
.service p{margin-top:8px;font-size:11px;line-height:22px;color:var(--muted);padding:0 10px}
.service .more{margin-top:8px;font-size:11px;color:var(--blue)}
.service .rule{margin-top:22px;height:1px;background:var(--line)}

/* featured */
.featured{left:0;top:1280px;width:1200px;height:465px;background:linear-gradient(135deg,#1c1c1c,#3a3a3a 50%,#1a1a1a)}
.featured .sec-title{top:80px;color:var(--white)}
.project{top:155px;width:228px;height:222px;background:var(--white);border:2px solid var(--white)}
.project-photo{height:156px}
.project-cap{position:relative;padding:10px 56px 0 10px;font-size:11px;line-height:19px;color:#333}
.play{position:absolute;right:12px;top:170px;width:32px;height:32px;border-radius:50%;background:var(--blue)}
.play::after{content:"";position:absolute;left:13px;top:10px;border-left:9px solid var(--white);border-top:6px solid transparent;border-bottom:6px solid transparent}

/* pricing */
.plan{top:1948px;width:295px;height:460px;border:1px solid var(--line);background:var(--white)}
.plan-head{position:relative;height:185px;text-align:center;color:var(--white);padding-top:26px}
.plan-head::after{content:"";position:absolute;left:50%;bottom:-18px;margin-left:-20px;border-left:20px solid transparent;border-right:20px solid transparent;border-top:18px solid currentColor}
.plan-head .name{font-size:14px;text-transform:uppercase}
.plan-head .price{margin-top:8px;font-family:"Roboto",Arial,sans-serif;font-size:48px;font-weight:700;line-height:56px}
.plan-head .price sup{font-size:20px;vertical-align:18px;margin-right:6px}
.plan-head .note{margin-top:6px;font-size:12px;line-height:20px;padding:0 50px}
.plan.orange .plan-head{background:var(--orange);color:var(--orange)}
.plan.blue .plan-head{background:var(--blue);color:var(--blue)}
.plan.dark .plan-head{background:var(--dark);color:var(--dark)}
.plan-head > *{color:var(--white)}
.plan ul{list-style:none;margin:32px 40px 0;font-size:11px;line-height:27px;color:#555;text-align:center}
.plan li{margin-bottom:2px}
.plan li i{display:inline-block;width:12px;height:12px;border-radius:50%;margin-right:6px;vertical-align:-1px}
.plan.orange li i{background:var(--orange)}.plan.blue li i{background:var(--blue)}.plan.dark li i{background:var(--dark)}
.plan .btn{position:absolute;left:72px;bottom:30px;width:150px;height:40px;line-height:40px}
.plan.orange .btn{background:var(--orange)}.plan.blue .btn{background:var(--blue)}.plan.dark .btn{background:var(--dark)}

/* partners */
.partners{left:0;top:2488px;width:1200px;height:128px;border-top:1px solid var(--line);display:flex;align-items:center;justify-content:center;gap:46px;font-family:"Roboto",Arial,sans-serif;font-size:22px;font-weight:700;color:#9b9b9b}

/* contact */
.contact{left:0;top:2616px;width:1200px;height:434px;background:var(--soft)}
.contact .sec-title{top:72px}
.label{font-size:14px;color:#333;text-transform:uppercase}
.field{background:var(--white);border:1px solid #ddd;font-size:10px;color:#999;padding:8px 14px}
.send{left:588px;top:310px;width:128px;height:40px;line-height:40px;background:var(--orange);font-weight:600}
.qc{left:815px;display:flex;align-items:center;gap:24px;font-size:11px;color:#666}
.qc-icon{width:36px;height:36px;border-radius:50%;border:1px solid var(--blue);display:flex;align-items:center;justify-content:center}

/* footer */
.footer-links{left:133px;top:3076px;font-size:10px;color:#333;word-spacing:2px}
.copyright{left:133px;top:3102px;font-size:9px;color:#666}
.connect{left:838px;top:3086px;display:flex;align-items:center;gap:8px;font-size:9px;color:#555}
.connect span.c{width:26px;height:26px;border-radius:50%}
</style>
</head>
<body>

<div class="abs topline"></div>
<header class="abs site-header">
  <div class="abs brand"><span class="brand-dot"></span><span class="brand-name">Dovin Sound 862</span></div>
  <nav class="abs nav"><span class="active">Home</span><span>About Us</span><span>Services</span><span>Recording</span><span>Blog</span><span style="margin-right:34px">Contact Us</span></nav>
  <svg class="abs search" width="18" height="18" viewBox="0 0 18 18"><circle cx="7.5" cy="7.5" r="5.5" fill="none" stroke="#f7860f" stroke-width="2"/><line x1="11.5" y1="11.5" x2="16" y2="16" stroke="#f7860f" stroke-width="2"/></svg>
</header>

<section class="abs hero" role="img" aria-label="Photo of a recording studio control room with a large mixing desk and monitor speakers">
  <h1 class="abs hero-title"><span class="l1">Music</span><span class="l2">Recording Studio</span></h1>
  <a class="abs btn hero-btn">View More Information</a>
  <svg class="abs hero-arrow prev" viewBox="0 0 52 52"><polyline points="30,16 20,26 30,36" fill="none" stroke="#fff" stroke-width="2"/></svg>
  <svg class="abs hero-arrow next" viewBox="0 0 52 52"><polyline points="22,16 32,26 22,36" fill="none" stroke="#fff" stroke-width="2"/></svg>
  <svg class="abs hero-curve" width="1200" height="140" viewBox="0 0 1200 140">
    <path d="M0,30 Q600,250 1200,30 L1200,140 L0,140 Z" fill="#fff"/>
    <path d="M0,30 Q600,250 1200,30" fill="none" stroke="#f7860f" stroke-width="7"/>
  </svg>
</section>

<h2 class="abs sec-title" style="top:784px">Our Services</h2>
<p class="abs sec-sub" style="top:834px">From first take to final master, our engineers shape every session with care, warm analog gear and a room built for focused, radio ready sound.</p>

<div class="abs service" style="left:130px">
  <div class="service-icon"><svg width="64" height="64" viewBox="0 0 64 64" fill="none" stroke="#2ec7f0" stroke-width="3"><path d="M24 46V14l26-6v32"/><circle cx="18" cy="46" r="6"/><circle cx="44" cy="40" r="6"/></svg></div>
  <h3>Vocal Tracking</h3>
  <p>Treated vocal booth, premium microphones and a patient engineer to capture your best performance in every single take.</p>
  <div class="more">Read More Info &rsaquo;</div><div class="rule"></div>
</div>
<div class="abs service" style="left:455px">
  <div class="service-icon"><svg width="70" height="70" viewBox="0 0 70 70" fill="none" stroke="#2ec7f0" stroke-width="3"><circle cx="35" cy="35" r="28"/><circle cx="35" cy="35" r="18"/><circle cx="35" cy="35" r="5"/><path d="M50 58l8-8"/></svg></div>
  <h3>Mixing Sessions</h3>
  <p>Balanced, punchy mixes built on a modern console with analog warmth and careful attention to every part of your song.</p>
  <div class="more">Read More Info &rsaquo;</div><div class="rule"></div>
</div>
<div class="abs service" style="left:780px">
  <div class="service-icon"><svg width="64" height="64" viewBox="0 0 64 64" fill="none" stroke="#2ec7f0" stroke-width="3"><path d="M8 16h20l4 6h24v30H8z"/><rect x="18" y="28" width="28" height="16" rx="2"/><circle cx="26" cy="36" r="3"/><circle cx="38" cy="36" r="3"/></svg></div>
  <h3>Mastering</h3>
  <p>Final polish for streaming, radio and vinyl so your record sounds loud, clear and consistent on any system.</p>
  <div class="more">Read More Info &rsaquo;</div><div class="rule"></div>
</div>

<section class="abs featured" role="img" aria-label="Dim studio background photo behind the featured projects">
  <h2 class="abs sec-title">Featured Projects</h2>
  <div class="abs project" style="left:133px">
    <div class="project-photo" role="img" aria-label="Photo of a mixing console with lit faders" style="background:linear-gradient(135deg,#1d3b5c,#3a6b8f 50%,#c46b2a)"></div>
    <div class="project-cap">Live Tracking Room<br>Session notes</div><span class="play"></span>
  </div>
  <div class="abs project" style="left:368px">
    <div class="project-photo" role="img" aria-label="Photo of a singer at a studio microphone" style="background:linear-gradient(135deg,#d9d6d0,#9a9690 60%,#5d5a56)"></div>
    <div class="project-cap">Vocal Booth Takes<br>Session notes</div><span class="play"></span>
  </div>
  <div class="abs project" style="left:603px">
    <div class="project-photo" role="img" aria-label="Photo of a studio condenser microphone with headphones" style="background:linear-gradient(135deg,#0f3a55,#2d7fae 55%,#0b1f30)"></div>
    <div class="project-cap">Microphone Lineup<br>Session notes</div><span class="play"></span>
  </div>
  <div class="abs project" style="left:838px">
    <div class="project-photo" role="img" aria-label="Photo of two musicians recording with a guitar" style="background:linear-gradient(135deg,#2b2a2e,#5a4a44 55%,#1b1b1d)"></div>
    <div class="project-cap">Acoustic Duo Set<br>Session notes</div><span class="play"></span>
  </div>
</section>

<h2 class="abs sec-title" style="top:1806px">Our Pricing</h2>
<p class="abs sec-sub" style="top:1855px">Simple hourly rates and membership packages for artists at every stage. Book a block and bring your next record to life.</p>

<div class="abs plan orange" style="left:133px">
  <div class="plan-head"><div class="name">Recording Price</div><div class="price"><sup>$</sup>80</div><div class="note">Per hour minimum 4 hours Required</div></div>
  <ul><li><i></i>$75 per hour minimum 8 hours required</li><li><i></i>$70 per hour minimum 12 hours required</li><li><i></i>$90 for individual hours, packages recommended</li></ul>
  <a class="btn">Book Now Today</a>
</div>
<div class="abs plan blue" style="left:454px">
  <div class="plan-head"><div class="name">Memberships Deals</div><div class="price"><sup>$</sup>1500</div><div class="note">Get 48 recording hours in addition to 24 hours mix down</div></div>
  <ul><li><i></i>$2500, get 72 recording hours in addition to 48 hours mix down</li><li style="margin-top:12px"><i></i>$3500, get 96 recording hours in addition to 72 hours mix down</li></ul>
  <a class="btn">Book Now Today</a>
</div>
<div class="abs plan dark" style="left:774px">
  <div class="plan-head"><div class="name">Mix Down Only Prices</div><div class="price"><sup>$</sup>50</div><div class="note">Per hour minimum 4 hours Required</div></div>
  <ul><li><i></i>$45 per hour minimum 8 hours required</li><li><i></i>$40 per hour minimum 12 hours required</li><li><i></i>$60 for individual hours, packages recommended</li></ul>
  <a class="btn">Book Now Today</a>
</div>

<div class="abs partners"><span>Northwave</span><span>Brightmoor</span><span>Ardent</span><span>TDL</span><span>Halden</span><span>vela</span><span>K.R.Lowell</span><span>Crestfield Review</span></div>

<section class="abs contact">
  <h2 class="abs sec-title">Contact Us</h2>
  <div class="abs label" style="left:133px;top:158px">Message Us</div>
  <div class="abs field" style="left:133px;top:180px;width:288px;height:32px">Name :</div>
  <div class="abs field" style="left:430px;top:180px;width:286px;height:32px">Email :</div>
  <div class="abs field" style="left:133px;top:220px;width:583px;height:72px">Message</div>
  <a class="abs btn send">Send Message</a>
  <div class="abs label" style="left:815px;top:158px">Quick Contact</div>
  <div class="abs qc" style="top:192px"><span class="qc-icon"><svg width="14" height="18" viewBox="0 0 14 18"><path d="M7 1a6 6 0 0 1 6 6c0 4-6 10-6 10S1 11 1 7a6 6 0 0 1 6-6z" fill="none" stroke="#2ec7f0" stroke-width="1.6"/><circle cx="7" cy="7" r="2" fill="#2ec7f0"/></svg></span>5176 Bellweather Ln, Larkfield, Fl, 34719</div>
  <div class="abs qc" style="top:254px"><span class="qc-icon"><svg width="18" height="14" viewBox="0 0 18 14"><rect x="1" y="1" width="16" height="12" fill="none" stroke="#2ec7f0" stroke-width="1.6"/><polyline points="1,1 9,8 17,1" fill="none" stroke="#2ec7f0" stroke-width="1.6"/></svg></span>Email: Mokaforsound@trellomail.net</div>
  <div class="abs qc" style="top:316px"><span class="qc-icon"><svg width="16" height="16" viewBox="0 0 16 16"><path d="M3 1l3 3-2 2c1 2 3 4 6 6l2-2 3 3-2 2C7 15 1 9 1 3z" fill="none" stroke="#2ec7f0" stroke-width="1.5"/></svg></span><span style="font-size:14px">Phone: 417-293-7041</span></div>
</section>

<footer>
  <div class="abs footer-links">HOME &nbsp;|&nbsp; ABOUT US &nbsp;|&nbsp; SERVICES &nbsp;|&nbsp; RECORDING &nbsp;|&nbsp; BLOG &nbsp;|&nbsp; CONTACT US</div>
  <div class="abs copyright">COPYRIGHT © DOVIN SOUND 862 , 2017 | ALLRIGHTS RESERVED.</div>
  <div class="abs connect">CONNECT WITH US : <span class="c" style="background:#3b5998"></span><span class="c" style="background:#2ec7f0"></span><span class="c" style="background:#d62d20"></span><span class="c" style="background:#a6804f"></span></div>
</footer>

</body>
</html>
```